Food and Beverage Business Cards

We need business cards with logo designs for a consultant in the food and beverage industry. We specialize in helping restaurants fix operational and management problems.
Specific areas of expertise include:
-Steps of service
-Staff management tools
-Standard operating procedures
-Profit and loss management
-Inventory
-Point of sales
-Bar Menu
-Mystery shopper service
-Handling and managing suppliers

Target Market(s)

Restaurant and bar owners and managers

Industry/Entity Type

Business

Contact Information for Business Card

Mathieu Girardot
Q&T Consulting
phone: 15027390614
mathqt@sampleinbox.com

Font styles to use
Other font styles liked:
• Check out the screen shot font idea

Colors

Designer to choose colors to be used in the design.

Requirements
Must have
• Must include QR code (See attachment)
• Logo should reflect our specific focus on the drinks side of the industry.
• Areas of Expertise:
• -Service Steps
• -Staff management tools
• -S.O.P
• -P&L Management
• -Inventory
• -P.O.S
• -Bar Menu
• -Mystery Shopper Service
• -Handling and Managing Suppliers

```html
<!DOCTYPE html>
<html lang="en">
<head>
<meta charset="UTF-8">
<title>Q&amp;T Consulting Business Cards</title>
<link rel="stylesheet" href="https://fonts.googleapis.com/css2?family=Open+Sans:wght@400;600;700&display=swap">
<style>
  :root {
    --backdrop: #2e2e30;
    --card-black: #111111;
    --card-white: #f4f4f4;
    --swoosh-grey: #8a8a8a;
    --text-light: #ffffff;
    --text-soft: #d6d6d6;
    --text-dark: #1a1a1a;
    --badge-green: #3f8f3a;
    --badge-grey: #cfcfcf;
  }
  * { margin: 0; padding: 0; box-sizing: border-box; }
  html, body {
    width: 1200px; height: 960px; overflow: hidden;
    background: var(--backdrop);
    font-family: "Open Sans", Arial, sans-serif;
  }
  .canvas {
    position: relative; width: 1200px; height: 960px;
  }
  .card {
    position: absolute; left: 250px; width: 700px; height: 400px;
    overflow: hidden;
    box-shadow: 0 12px 30px rgba(0,0,0,0.45);
  }
  /* Back of card */
  .card-back { top: 50px; background: var(--card-black); color: var(--text-light); }
  .badges {
    position: absolute; top: 26px; right: 30px; display: flex; gap: 12px;
  }
  .badge { width: 44px; height: 44px; border-radius: 50%; }
  .badge-green { background: var(--badge-green); }
  .badge-grey { background: var(--badge-grey); border: 3px solid #666; }
  .back-brand {
    position: absolute; top: 118px; left: 0; right: 0; text-align: center;
    font-size: 52px; font-weight: 600; letter-spacing: 1px; color: var(--text-light);
  }
  .expertise {
    position: absolute; top: 215px; left: 0; right: 0; text-align: center;
  }
  .expertise-title { font-size: 22px; font-weight: 700; margin-bottom: 8px; }
  .expertise-line { font-size: 16px; color: var(--text-soft); line-height: 1.5; }
  /* Front of card */
  .card-front { top: 510px; background: var(--card-white); }
  .front-shape { position: absolute; inset: 0; }
  .front-brand {
    position: absolute; top: 140px; left: 330px; width: 340px; text-align: center;
    font-size: 50px; font-weight: 600; color: var(--text-dark); letter-spacing: 1px;
  }
  .contact {
    position: absolute; left: 30px; top: 222px; color: var(--text-light);
  }
  .contact-name { font-size: 22px; font-weight: 700; text-transform: uppercase; }
  .contact-role { font-size: 17px; text-transform: uppercase; margin-bottom: 12px; }
  .contact-item { display: flex; align-items: center; gap: 10px; font-size: 17px; line-height: 1.5; }
  .contact-item svg { width: 16px; height: 16px; fill: var(--text-light); }
</style>
</head>
<body>
<main class="canvas">
  <section class="card card-back">
    <div class="badges">
      <span class="badge badge-green"></span>
      <span class="badge badge-grey"></span>
      <span class="badge badge-grey"></span>
    </div>
    <div class="back-brand">Q&amp;T Ridgeway</div>
    <div class="expertise">
      <h2 class="expertise-title">Areas of Expertise</h2>
      <p class="expertise-line">Service Steps | Staff management tools | S.O.P | P&amp;L Management</p>
      <p class="expertise-line">Inventory | P.O.S | Bar Menu | Mystery Shopper Service</p>
      <p class="expertise-line">Handling and Managing Suppliers</p>
    </div>
  </section>

  <section class="card card-front">
    <svg class="front-shape" viewBox="0 0 700 400" preserveAspectRatio="none">
      <path d="M0,0 H132 C270,60 230,300 372,400 H0 Z" fill="var(--swoosh-grey)"/>
      <path d="M0,0 H112 C250,60 205,300 340,400 H0 Z" fill="var(--card-black)"/>
    </svg>
    <div class="front-brand">Q&amp;T Ridgeway</div>
    <div class="contact">
      <p class="contact-name">Mathieu Girardot</p>
      <p class="contact-role">Q&amp;T Consulting</p>
      <p class="contact-item">
        <svg viewBox="0 0 16 16"><path d="M3 2h3l1 3-2 1c1 2 2 3 4 4l1-2 3 1v3c0 1-1 2-2 2C6 14 2 10 2 4c0-1 0-2 1-2z"/></svg>
        15027390614
      </p>
      <p class="contact-item">
        <svg viewBox="0 0 16 16"><path d="M1 3h14v10H1z M2 4l6 5 6-5" fill="none" stroke="#fff" stroke-width="1.5"/></svg>
        mathqt@sampleinbox.com
      </p>
    </div>
  </section>
</main>
</body>
</html>
```